my website is tavorinque.com. (brand name is ta belle vitrine) This is just a template that i have choose for. The content and the pictures are not about my business just the template.
I would like to have 4 pages for now. 1 homepage, which will be an overview for all pages, it is right now in this way. It will directly highlight my story. My website will tell an exclusive story about details which makes the difference and will make people happy with very small things. It will be art related but very stylish as well. I also want to have a event agenda on my homepage where people can see where my next event is. Page 2 my blog, where I will write weekly about mindset, lifestyle and details. Inspiration place for people who are looking for unique and exclusive approaches in life. Page 3 shop, where I will sell my stuff which is handmade and unique, it will be limited edition stuff. Mostly I will make the designs from marbling art, which I am a teacher for. (https://www.vidoranta.com/watch?v=KpwuzRaxTmo) check this video out for more. Page 4 is book page. Here people will be able to book private or group classes for marbling art (check the video). I have already a community of more than 500 people on gath rix, which will be my public as well. I wanna implement the gath rix button on this page as well. to be able to track.

This is about my website. I also need a logo for my brand, which will suit my website and my goals.

I can also give you a reference website, which really like as structure and style;
https://www.brightorvalco.com/products/the-morning-ledger?gclid=Xr4TpLmwq2HsVD9KEBsZTrc-WkPhyQ-uvlEjdRs3NKaOYFCBWMpuTzG8xyCVbhdnLWRqoaNf_2e8ZtpRvHbAwq9FLQ_hqgQ

Logo Text

ta belle vitrine

Coding

Coded - Design and coding required

Number of Pages Required

4 page

Requirements
Must have
• I can also give you a reference website, which really like as structure and style;
• https://www.brightorvalco.com/products/the-morning-ledger?gclid=Xr4TpLmwq2HsVD9KEBsZTrc-WkPhyQ-uvlEjdRs3NKaOYFCBWMpuTzG8xyCVbhdnLWRqoaNf_2e8ZtpRvHbAwq9FLQ_hqgQ

```html
<!DOCTYPE html>
<html lang="en">
<head>
<meta charset="utf-8">
<title>Shop — ta belle vitrine</title>
<link href="https://fonts.googleapis.com/css2?family=Montserrat:wght@400;500&family=Lato:wght@300;400&display=swap" rel="stylesheet">
<style>
  :root {
    --ink: #1f1c1d;
    --text: #555555;
    --muted: #7a7a7a;
    --white: #ffffff;
    --hero-dark: #2b2320;
    --hero-warm: #5a4a2e;
    --line: #2a2a2a;
  }
  * { margin: 0; padding: 0; box-sizing: border-box; }
  html, body { width: 1200px; height: 1200px; overflow: hidden; background: var(--white); }
  body { position: relative; font-family: 'Lato', sans-serif; color: var(--text); }

  .video-hero {
    position: absolute; left: 0; top: 0; width: 1200px; height: 390px;
    background:
      linear-gradient(180deg, rgba(20,14,12,0.55) 0%, rgba(20,14,12,0.35) 60%, rgba(20,14,12,0.45) 100%),
      radial-gradient(ellipse at 30% 75%, #6b5a24 0%, transparent 45%),
      radial-gradient(ellipse at 70% 80%, #6a3a2a 0%, transparent 45%),
      linear-gradient(180deg, #3a2426 0%, #3b3228 30%, #4a4226 100%);
  }
  .video-hero__title {
    position: absolute; top: 121px; left: 0; width: 100%; text-align: center;
    font-family: 'Montserrat', sans-serif; font-weight: 500; font-size: 18px;
    letter-spacing: 0.5px; color: var(--white);
  }
  .video-hero__play { position: absolute; left: 570px; top: 174px; width: 57px; height: 57px; }

  .shop-heading {
    position: absolute; top: 444px; left: 0; width: 100%; text-align: center;
    font-family: 'Montserrat', sans-serif; font-weight: 400; font-size: 17px;
    letter-spacing: 1px; color: var(--ink);
  }
  .shop-subheading {
    position: absolute; top: 474px; left: 0; width: 100%; text-align: center;
    font-family: 'Lato', sans-serif; font-weight: 300; font-size: 9.5px;
    letter-spacing: 2px; color: var(--muted);
  }
  .shop-rule { position: absolute; top: 502px; left: 542px; width: 128px; height: 1px; background: var(--line); }

  .shop-intro {
    position: absolute; top: 556px; left: 330px; width: 545px; text-align: center;
    font-size: 10.5px; line-height: 18.8px; letter-spacing: 0.8px; color: var(--text);
  }

  .shop-tab {
    position: absolute; top: 670px; height: 38px;
    display: flex; align-items: center; justify-content: center;
    border: 1px solid var(--ink); background: var(--white);
    font-family: 'Montserrat', sans-serif; font-weight: 500; font-size: 9.5px;
    letter-spacing: 0.3px; color: var(--ink);
  }
  .shop-tab--active { background: var(--ink); color: var(--white); }

  .product-tile { position: absolute; width: 277px; height: 277px; }
  .product-tile--row2 { height: 140px; }
</style>
</head>
<body>

<section class="video-hero" role="img" aria-label="Dimmed photo of a marbling tray with floral paint patterns and paint jars behind">
  <h2 class="video-hero__title">SEE OUR VIDEO</h2>
  <svg class="video-hero__play" viewBox="0 0 57 57" aria-label="Play video">
    <circle cx="28.5" cy="28.5" r="28.5" fill="#ffffff"/>
    <path d="M23 20 L38 28.5 L23 37 Z" fill="#1f1c1d"/>
  </svg>
</section>

<h1 class="shop-heading">SHOP</h1>
<p class="shop-subheading">SHOP OUR BEST WORK SO FAR</p>
<div class="shop-rule"></div>

<p class="shop-intro">Donec rutrum congue leo eget malesuada. Curabitur non nulla sit amet nisl tempus convallis quis ac lectus. Sed porttitor lectus nibh. Proin eget tortor risus. Nulla porttitor accumsan tincidunt. Nulla porttitor accumsan tincidunt.</p>

<nav>
  <a class="shop-tab shop-tab--active" style="left:334px;width:105px;">PRODUCT</a>
  <a class="shop-tab" style="left:461px;width:129px;">SHIPPING</a>
  <a class="shop-tab" style="left:611px;width:115px;">BULK ORDERS</a>
  <a class="shop-tab" style="left:748px;width:111px;">FAQs</a>
</nav>

<div class="product-tile" style="left:162px;top:768px;background:linear-gradient(180deg,#4a4038 0%,#5c4a3e 28%,#9a6a56 40%,#8a5a48 100%);" role="img" aria-label="Marbling tray with brown and white patterns, paint jars behind"></div>
<div class="product-tile" style="left:462px;top:768px;background:radial-gradient(ellipse at 40% 20%,#c9a08e 0%,transparent 40%),linear-gradient(160deg,#a77466 0%,#8e5e56 60%,#7a4f48 100%);" role="img" aria-label="Hand drawing a stylus through pink marbled paint"></div>
<div class="product-tile" style="left:762px;top:768px;background:linear-gradient(170deg,#7a7a3a 0%,#4a6a5a 30%,#8a6a9a 60%,#6a2a22 100%);" role="img" aria-label="Purple and white marbling pattern with brushes"></div>

<div class="product-tile product-tile--row2" style="left:162px;top:1069px;height:131px;background:linear-gradient(180deg,#6a5a4a 0%,#7a3a4a 45%,#3a3436 80%,#2a2628 100%);" role="img" aria-label="Paint jars with brushes beside a marbling tray"></div>
<div class="product-tile product-tile--row2" style="left:462px;top:1069px;height:131px;background:linear-gradient(180deg,#7a2226 0%,#5a4a3a 45%,#8ab0a0 75%,#6aa08a 100%);" role="img" aria-label="Paint jars above a colourful floral marbling tray"></div>
<div class="product-tile product-tile--row2" style="left:762px;top:1069px;height:131px;background:linear-gradient(180deg,#6a5a4a 0%,#7a3a4a 45%,#3a3436 80%,#2a2628 100%);" role="img" aria-label="Paint jars with brushes beside a marbling tray"></div>

</body>
</html>
```